Brimsett Gardening Fresh New Website

We are looking to create a simple fresh website for our landscaping business. The website should appeal to a 'high end' audience. We deal with a lot of Embassies and affluent clients who have extremely large gardens that are meticulously maintained. The site is about communicating our excellent landscaping and customer service skills and encouraging new clients to reach out and engage us to take care of their gardens.

The website is basically going to be our business card, it will have almost no functionality other than two 'contact us' forms, one for smaller clients and one for more detailed projects.

The website will not have a lot of written content and will have to show photos of beautifully landscaped gardens.

The main logo in black will influence the site, however, we are open to all suggestions.

We are expecting to have the following pages:
Home Page
Services
About Us
Contact Us
Showcase (photo gallery of our work)

We need someone who can code it to wordpress and be available for minor changes over a number of days. They will be simple tweaks.

```html
<!DOCTYPE html>
<html lang="en">
<head>
<meta charset="utf-8">
<title>Brimsett Gardening</title>
<link href="https://fonts.googleapis.com/css2?family=Poppins:wght@400;500;600;700&family=Libre+Baskerville:wght@400;700&display=swap" rel="stylesheet">
<style>
:root{
  --ink:#151311;
  --dark:#1b1916;
  --gold:#b07a1f;
  --gold-dark:#9c6a17;
  --gold-light:#f4d14a;
  --cream:#fdf0dd;
  --mist:#eff1ec;
  --text:#2a2a2a;
  --muted:#6b6b6b;
  --line:#d9d9d9;
  --white:#ffffff;
}
*{box-sizing:border-box;margin:0;padding:0}
html,body{width:1200px;height:4458px;overflow:hidden;background:var(--white)}
body{font-family:'Poppins',sans-serif;color:var(--text);position:relative}
.page{position:relative;width:1200px;height:4458px;overflow:hidden}
.abs{position:absolute}
.serif{font-family:'Libre Baskerville',serif}
.btn{position:absolute;display:flex;align-items:center;justify-content:center;background:var(--gold);color:#fff;font-weight:600;font-size:11px;border-radius:3px;letter-spacing:.3px}
.btn-grad{background:linear-gradient(90deg,#b8862c,var(--gold-light));color:var(--ink)}

/* header */
.header{position:absolute;left:0;top:0;width:1200px;height:90px;background:var(--ink);color:#fff}
.header .rule{position:absolute;top:46px;height:1px;background:#4a4540}
.social{position:absolute;top:17px;width:14px;height:14px;border:1.5px solid #cfc7bb;border-radius:50%}
.nav-link{position:absolute;top:58px;font-size:12px;color:#fff}
.brand-mark{position:absolute;left:527px;top:10px;width:100px;text-align:center;color:var(--gold)}
.brand-mark .dot{width:18px;height:18px;border:1.5px solid var(--gold);border-radius:50%;margin:0 auto 5px}
.brand-mark .name{font-family:'Poppins',sans-serif;font-size:10px;letter-spacing:3px;font-weight:500}

/* hero */
.hero{position:absolute;left:0;top:90px;width:1200px;height:566px;background:linear-gradient(180deg,#7d8378 0%,#5d6957 35%,#3f4f30 65%,#2e3b20 100%)}
.hero-shade{position:absolute;inset:0;background:rgba(0,0,0,.28)}
.hero-kicker{position:absolute;top:290px;width:1200px;text-align:center;color:#fff;font-size:24px;letter-spacing:4px;font-weight:500}
.hero-title{position:absolute;top:330px;width:1200px;text-align:center;color:#fff;font-size:46px;line-height:57px;font-weight:700}

/* quote form */
.quote{position:absolute;left:694px;top:610px;width:371px;height:441px;background:var(--ink);border:4px solid var(--gold)}
.quote h3{position:absolute;left:24px;top:24px;font-size:20px;line-height:27px;color:#fff;font-weight:700}
.quote h3 span{color:var(--gold-light)}
.qfield{position:absolute;left:24px;width:315px;height:34px;border:1px solid #cfcfcf;color:#fff;font-size:11px;padding:9px 13px}
.qfield i{color:#e23b3b;font-style:normal}

/* about */
.about-h{position:absolute;left:142px;top:707px;font-size:35px;font-weight:700;color:var(--ink);line-height:46px}
.about-h2{position:absolute;left:142px;top:753px;font-size:35px;font-weight:700;color:var(--gold);line-height:46px}
.about-p{position:absolute;left:142px;width:440px;font-size:11.5px;line-height:22.5px;color:#333}

/* sections */
.section-title{position:absolute;width:1200px;text-align:center;font-size:34px;font-weight:700;color:var(--ink)}
.section-title span{color:var(--gold)}
.services-bg{position:absolute;left:0;top:1120px;width:1200px;height:700px;background:linear-gradient(180deg,#edf0ea,#f3f5f0 60%,#eceee8)}
.card{position:absolute;top:1333px;width:218px;height:255px;border-radius:10px;overflow:hidden}
.card .shade{position:absolute;inset:0;background:linear-gradient(180deg,rgba(0,0,0,0) 35%,rgba(0,0,0,.7))}
.card h4{position:absolute;left:0;right:0;top:134px;text-align:center;color:#fff;font-size:15px;font-weight:600}
.card p{position:absolute;left:18px;right:18px;top:162px;text-align:center;color:#fff;font-size:11px;line-height:18px}
.card a{position:absolute;left:0;right:0;top:206px;text-align:center;color:#fff;font-size:11px;font-weight:600;text-decoration:underline}
.photo{position:absolute;border-radius:14px}

/* testimonials */
.testi-bg{position:absolute;left:0;top:2732px;width:1200px;height:620px;background:var(--cream)}
.tcard{position:absolute;top:2937px;width:292px;height:284px;background:#fff;border-radius:12px;box-shadow:0 4px 14px rgba(0,0,0,.06)}
.stars{position:absolute;left:27px;top:27px;color:var(--gold);font-size:16px;letter-spacing:4px}
.badge{position:absolute;right:26px;top:26px;width:22px;height:22px;border:3px solid #9a9a9a;border-radius:50%}
.tcard p{position:absolute;left:27px;right:20px;top:76px;font-size:12px;line-height:21px;color:#333}
.tcard .who{position:absolute;left:27px;top:232px;font-size:15px;font-weight:600;font-style:italic;color:var(--ink)}
.arrow{position:absolute;top:3051px;width:54px;height:54px;border-radius:50%}

/* contact */
.contact-card{position:absolute;left:142px;top:3463px;width:914px;height:430px;background:#fff;border-radius:18px;box-shadow:0 6px 24px rgba(0,0,0,.07)}
.contact-panel{position:absolute;left:142px;top:3463px;width:332px;height:430px;border-radius:18px;background:linear-gradient(160deg,#2a2823,#171613 60%,#25221c)}
.cp-kicker{position:absolute;left:177px;top:3524px;font-size:12px;font-weight:600;color:var(--gold);letter-spacing:.5px}
.cp-title{position:absolute;left:177px;top:3550px;font-size:25px;line-height:38px;color:#fff;font-weight:500}
.cp-row{position:absolute;left:177px;display:flex;align-items:center;gap:12px;color:#fff;font-size:12px;line-height:19px}
.ico{width:28px;height:28px;border:1.5px solid #fff;border-radius:50%;display:flex;align-items:center;justify-content:center;flex:none}
.cfield{position:absolute;height:35px;border:1px solid var(--line);font-size:11px;color:#555;padding:10px 17px}

/* footer */
.footer{position:absolute;left:0;top:4061px;width:1200px;height:397px;background:linear-gradient(180deg,#27241f,#141311)}
.f-logo{position:absolute;left:514px;top:4021px;width:174px;height:174px;border-radius:50%;background:var(--ink);border:3px solid var(--gold);text-align:center;color:var(--gold)}
.f-link{position:absolute;top:4246px;font-size:13px;color:#fff;font-weight:500}
.f-rule{position:absolute;left:142px;width:916px;height:1px;background:#6e6a62}
.f-info{position:absolute;top:4332px;display:flex;align-items:center;gap:10px;color:#fff;font-size:12px;line-height:20px}
</style>
</head>
<body>
<div class="page">

<!-- Header -->
<header class="header">
  <span class="social" style="left:139px"></span>
  <span class="social" style="left:165px"></span>
  <span class="social" style="left:193px"></span>
  <div class="rule" style="left:140px;width:290px"></div>
  <div class="rule" style="left:774px;width:285px"></div>
  <div class="abs" style="left:957px;top:15px;display:flex;align-items:center;gap:7px;font-size:12px">
    <svg width="14" height="14" viewBox="0 0 24 24" fill="none" stroke="#fff" stroke-width="2"><path d="M22 16.9v3a2 2 0 0 1-2.2 2 19.8 19.8 0 0 1-8.6-3.1 19.5 19.5 0 0 1-6-6A19.8 19.8 0 0 1 2.1 4.2 2 2 0 0 1 4.1 2h3a2 2 0 0 1 2 1.7c.1 1 .4 1.9.7 2.8a2 2 0 0 1-.5 2.1L8 9.9a16 16 0 0 0 6 6l1.3-1.3a2 2 0 0 1 2.1-.4c.9.3 1.8.6 2.8.7a2 2 0 0 1 1.7 2z"/></svg>
    123 456 7890
  </div>
  <a class="nav-link" style="left:140px">Home</a>
  <a class="nav-link" style="left:246px">Services</a>
  <a class="nav-link" style="left:366px">Gallery</a>
  <div class="brand-mark"><div class="dot"></div><div class="name">BRIMSETT<br>GARDENING</div></div>
  <a class="nav-link" style="left:714px">About Us</a>
  <a class="nav-link" style="left:837px">Contact Us</a>
  <a class="nav-link" style="left:971px">Projects For
    <svg width="12" height="8" viewBox="0 0 12 8" style="margin-left:4px"><path d="M1 1l5 5 5-5" stroke="#fff" stroke-width="1.6" fill="none"/></svg></a>
</header>

<!-- Hero -->
<section class="hero" role="img" aria-label="Large house with a manicured front garden, hedges and red flower beds">
  <div class="hero-shade"></div>
</section>
<div class="hero-kicker">LANDSCAPE PROS</div>
<h1 class="hero-title serif">Stunning Landscapes To<br>Inspire Your Family</h1>
<div class="btn btn-grad" style="left:535px;top:455px;width:130px;height:30px">Request A Quote</div>

<!-- About -->
<h2 class="about-h serif">About</h2>
<h2 class="about-h2 serif">Brimsett Gardening</h2>
<p class="about-p" style="top:806px">Lorem Ipsum Is Simply Dummy Text Of The Printing And Typesetting Industry. Lorem Ipsum Has Been The Industry's Standard Dummy Text Ever Since The 1500s, When An Unknown Printer Took A Galley Of Type And Scrambled It To Make A Type Specimen Book.</p>
<p class="about-p" style="top:903px">Lorem Ipsum Is Simply Dummy Text Of The Printing And Typesetting Industry. Lorem Ipsum Has Been The Industry's Standard Dummy Text Ever Since The 1500s, When &nbsp;And Scrambled It To Make A Type Specimen Book.</p>
<div class="btn btn-grad" style="left:142px;top:990px;width:92px;height:32px">Read More</div>

<!-- Quote form -->
<form class="quote">
  <h3 class="serif"><span>24% Off</span> For New<br>Landscape Services</h3>
  <div class="qfield" style="top:86px">Name<i>*</i></div>
  <div class="qfield" style="top:127px">Email<i>*</i></div>
  <div class="qfield" style="top:171px">Phone Number<i>*</i></div>
  <div class="qfield" style="top:212px">Street Address &amp; Zip Code<i>*</i></div>
  <div class="qfield" style="top:254px">Which Service Would You Like A Bill For?
    <svg class="abs" style="right:12px;top:13px" width="12" height="8" viewBox="0 0 12 8"><path d="M1 1l5 5 5-5" stroke="#fff" stroke-width="1.6" fill="none"/></svg></div>
  <div class="qfield" style="top:297px;height:69px">Message</div>
  <div class="btn btn-grad" style="left:24px;top:376px;width:315px;height:33px">Request A Quote</div>
</form>

<!-- Services -->
<div class="services-bg" role="img" aria-label="Faded park scene with trees behind the services"></div>
<svg class="abs" style="left:0;top:1110px" width="1200" height="40" viewBox="0 0 1200 40" preserveAspectRatio="none"><path d="M0 0H1200V28Q600 -6 0 28Z" fill="#fff"/></svg>
<svg class="abs" style="left:0;top:1750px" width="1200" height="72" viewBox="0 0 1200 72" preserveAspectRatio="none"><path d="M0 40Q600 -10 1200 40V72H0Z" fill="#fff"/></svg>
<h2 class="section-title" style="top:1245px">Our <span>Services</span></h2>

<div class="card" style="left:142px"><div class="abs" style="inset:0;background:linear-gradient(180deg,#3d4a4b,#2e3e25 60%,#2a3a14)" role="img" aria-label="Lone tree on a green lawn at dusk"></div><div class="shade"></div><h4>Landscaping</h4><p>Lorem ipsum dolor sit amet, consectetur adipiscing.</p><a>Read More</a></div>
<div class="card" style="left:374px"><div class="abs" style="inset:0;background:linear-gradient(180deg,#6e4a34,#4f4430 55%,#3a3522)" role="img" aria-label="Gardener trimming a lawn edge"></div><div class="shade"></div><h4>Lawn Service</h4><p>Lorem ipsum dolor sit amet, consectetur adipiscing.</p><a>Read More</a></div>
<div class="card" style="left:608px"><div class="abs" style="inset:0;background:linear-gradient(180deg,#7d7d70,#5e6b45 50%,#33401f)" role="img" aria-label="Wheelbarrow full of grass clippings"></div><div class="shade"></div><h4>Lawn Maintenance</h4><p>Lorem ipsum dolor sit amet, consectetur adipiscing.</p><a>Read More</a></div>
<div class="card" style="left:840px"><div class="abs" style="inset:0;background:linear-gradient(180deg,#707465,#6b5a45 50%,#4a4a3a)" role="img" aria-label="Arborists working among forest trees"></div><div class="shade"></div><h4>Tree Services</h4><p>Lorem ipsum dolor sit amet, consectetur adipiscing.</p><a>Read More</a></div>

<div class="btn" style="left:518px;top:1640px;width:165px;height:36px">VIEW ALL SERVICES</div>

<!-- Gallery -->
<h2 class="section-title" style="top:1868px">Our <span>Gallery</span></h2>
<div class="photo" style="left:142px;top:1967px;width:291px;height:293px;background:linear-gradient(160deg,#7ea84a,#3f6b2a 55%,#506048)" role="img" aria-label="Boardwalk through a lush garden"></div>
<div class="photo" style="left:454px;top:1967px;width:291px;height:293px;background:linear-gradient(180deg,#6d8f3c,#4c7a2b 55%,#8a8a82)" role="img" aria-label="Path under green garden arches"></div>
<div class="photo" style="left:764px;top:1967px;width:292px;height:293px;background:linear-gradient(180deg,#2e8fe0,#a7d7f5 40%,#d8442e 55%,#4fae2a 70%,#3d9a1f)" role="img" aria-label="Red flower beds on a bright lawn under blue sky"></div>
<div class="photo" style="left:142px;top:2279px;width:291px;height:292px;background:linear-gradient(180deg,#d3b8a0,#c98a3e 40%,#8fae3a 75%,#e9e4d8)" role="img" aria-label="Autumn park with a white picket fence"></div>
<div class="photo" style="left:454px;top:2279px;width:291px;height:292px;background:linear-gradient(160deg,#4e7a2a,#7fb83e 50%,#c9d6c8 70%,#4c8a28)" role="img" aria-label="Stone steps across a lawn beside a waterfall"></div>
<div class="photo" style="left:764px;top:2279px;width:292px;height:292px;background:linear-gradient(180deg,#5f7348,#b7b1a5 45%,#4f7a32 75%,#9d978c)" role="img" aria-label="Stone gazebo in a formal garden"></div>
<div class="btn" style="left:525px;top:2620px;width:150px;height:36px">VIEW ALL GALLERY</div>

<!-- Testimonials -->
<div class="testi-bg"></div>
<svg class="abs" style="left:0;top:2722px" width="1200" height="40" viewBox="0 0 1200 40" preserveAspectRatio="none"><path d="M0 0H1200V22Q600 -6 0 22Z" fill="#fff"/></svg>
<svg class="abs" style="left:0;top:3312px" width="1200" height="42" viewBox="0 0 1200 42" preserveAspectRatio="none"><path d="M0 26Q600 -6 1200 26V42H0Z" fill="#fff"/></svg>
<h2 class="section-title" style="top:2840px">Client <span>Testimonials</span></h2>

<div class="tcard" style="left:142px"><div class="stars">★★★★★</div><span class="badge"></span><p>Lorem ipsum dolor sit amet, consecte-tur adipiscing elit, sed do eiusmod tempor incididunt ut labore et dolore magna aliqua. Quis ipsum sus-pendisse ultrices gravida. Risus com-modo viverra maecenas accumsan lacus vel facilisis.</p><div class="who">Marta Hale</div></div>
<div class="tcard" style="left:454px"><div class="stars">★★★★★</div><span class="badge"></span><p>Lorem ipsum dolor sit amet, consecte-tur adipiscing elit, sed do eiusmod tempor incididunt ut labore et dolore magna aliqua. Quis ipsum sus-pendisse ultrices gravida. Risus com-modo viverra maecenas accumsan lacus vel facilisis.</p><div class="who">Marta Hale</div></div>
<div class="tcard" style="left:766px"><div class="stars">★★★★★</div><span class="badge"></span><p>Lorem ipsum dolor sit amet, consecte-tur adipiscing elit, sed do eiusmod tempor incididunt ut labore et dolore magna aliqua. Quis ipsum sus-pendisse ultrices gravida. Risus com-modo viverra maecenas accumsan lacus vel facilisis.</p><div class="who">Marta Hale</div></div>

<div class="arrow" style="left:65px;border:2px solid var(--gold)"><svg width="50" height="50" viewBox="0 0 50 50"><path d="M29 16l-9 9 9 9" stroke="#b07a1f" stroke-width="3" fill="none"/></svg></div>
<div class="arrow" style="left:1080px;background:var(--gold)"><svg width="54" height="54" viewBox="0 0 54 54"><path d="M23 18l9 9-9 9" stroke="#fff" stroke-width="3" fill="none"/></svg></div>

<!-- Contact -->
<div class="contact-card"></div>
<div class="contact-panel" role="img" aria-label="Dark garden backdrop behind contact details"></div>
<div class="cp-kicker">CONTACT US</div>
<div class="cp-title">Ask One Of Our<br>Experts For Help</div>
<div class="cp-row" style="top:3647px"><span class="ico"><svg width="13" height="13" viewBox="0 0 24 24" fill="none" stroke="#fff" stroke-width="2"><path d="M22 16.9v3a2 2 0 0 1-2.2 2 19.8 19.8 0 0 1-8.6-3.1 19.5 19.5 0 0 1-6-6A19.8 19.8 0 0 1 2.1 4.2 2 2 0 0 1 4.1 2h3a2 2 0 0 1 2 1.7c.1 1 .4 1.9.7 2.8a2 2 0 0 1-.5 2.1L8 9.9a16 16 0 0 0 6 6l1.3-1.3a2 2 0 0 1 2.1-.4c.9.3 1.8.6 2.8.7a2 2 0 0 1 1.7 2z"/></svg></span>+91 123-456-7890</div>
<div class="cp-row" style="top:3700px"><span class="ico"><svg width="14" height="11" viewBox="0 0 24 18" fill="none" stroke="#fff" stroke-width="2"><rect x="1" y="1" width="22" height="16" rx="2"/><path d="M1 2l11 8 11-8"/></svg></span>hello@brimsettgardening.com</div>
<div class="cp-row" style="top:3752px"><span class="ico"><svg width="12" height="14" viewBox="0 0 20 24" fill="none" stroke="#fff" stroke-width="2"><path d="M10 23s8-7.5 8-13a8 8 0 0 0-16 0c0 5.5 8 13 8 13z"/><circle cx="10" cy="10" r="3"/></svg></span>Lorem Ipsum is simply of the<br>printing and typesetting industry.</div>

<div class="abs" style="left:516px;top:3498px;font-size:15px;font-weight:600;color:var(--ink)">DROP YOUR MESSAGE</div>
<div class="cfield" style="left:514px;top:3550px;width:248px;border-color:var(--gold);color:var(--ink)">First Name</div>
<div class="cfield" style="left:772px;top:3550px;width:248px">Last Name</div>
<div class="cfield" style="left:514px;top:3598px;width:248px">Email Address</div>
<div class="cfield" style="left:772px;top:3598px;width:248px">Phone</div>
<div class="cfield" style="left:514px;top:3649px;width:506px;height:135px">Message</div>
<div class="btn" style="left:514px;top:3815px;width:128px;height:36px">SUBMIT NOW</div>

<!-- Footer -->
<footer class="footer" role="img" aria-label="Dark forest backdrop"></footer>
<div class="f-logo"><div style="margin:44px auto 12px;width:26px;height:26px;border:2px solid var(--gold);border-radius:50%"></div><div style="font-size:14px;letter-spacing:4px;font-weight:500;line-height:22px">BRIMSETT<br>GARDENING</div></div>
<a class="f-link" style="left:378px">Home</a>
<a class="f-link" style="left:450px">About Us</a>
<a class="f-link" style="left:543px">Services</a>
<a class="f-link" style="left:632px">Our Gallery</a>
<a class="f-link" style="left:742px">Contact Us</a>
<div class="f-rule" style="top:4307px"></div>
<div class="f-info" style="left:143px"><svg width="18" height="20" viewBox="0 0 20 24" fill="none" stroke="#fff" stroke-width="2"><path d="M10 23s8-7.5 8-13a8 8 0 0 0-16 0c0 5.5 8 13 8 13z"/><circle cx="10" cy="10" r="3"/></svg><span>Lorem Ipsum is simply dummy text<br>of the printing and typesetting.</span></div>
<div class="f-info" style="left:506px"><svg width="18" height="18" viewBox="0 0 24 24" fill="none" stroke="#fff" stroke-width="2"><path d="M22 16.9v3a2 2 0 0 1-2.2 2 19.8 19.8 0 0 1-8.6-3.1 19.5 19.5 0 0 1-6-6A19.8 19.8 0 0 1 2.1 4.2 2 2 0 0 1 4.1 2h3a2 2 0 0 1 2 1.7c.1 1 .4 1.9.7 2.8a2 2 0 0 1-.5 2.1L8 9.9a16 16 0 0 0 6 6l1.3-1.3a2 2 0 0 1 2.1-.4c.9.3 1.8.6 2.8.7a2 2 0 0 1 1.7 2z"/></svg><span>Call Us<br>123-456-7890</span></div>
<div class="f-info" style="left:798px"><svg width="20" height="16" viewBox="0 0 24 18" fill="none" stroke="#fff" stroke-width="2"><rect x="1" y="1" width="22" height="16" rx="2"/><path d="M1 2l11 8 11-8"/></svg><span>Email<br>hello@brimsettgardening.com</span></div>
<div class="f-rule" style="top:4390px"></div>
<div class="abs" style="left:0;top:4417px;width:1200px;text-align:center;color:#fff;font-size:12px">© 2024 Brimsett Gardening. All Rights Reserved.</div>

</div>
</body>
</html>
```